real esate business card with company logo and name

we need a business card design for a real esate company

The company name is Walsh & Brand Pty Ltd, and we have our logo designed and will upload. We want classic or moden feel. Black or white background. looks more textured. Should include folowinginformations
Owen Walsh and Lucy Brand
Sales Agents & Onsite Manager
p: 07 5948 2063
F: 07 5948 2174
M:0431 857 219
3/42 Marlow Crescent, FERNLEA QLD 4213

We want this business card looks professonal. Thank you in advance.

Industry/Entity Type

Real Estate Agent

Contact Information for Business Card

Owen Walsh and Lucy Brand
Onsite Manager & Sales Agents
p: 07 5948 2063
M:0431 857 219

Font styles to use
Serif

Colors
000000
fbfbfb
333333
959595

Requirements
Must have
• company logo and name, black or white back ground

```html
<!DOCTYPE html>
<html lang="en">
<head>
<meta charset="utf-8">
<title>Walsh &amp; Brand Pty Ltd — Business Card</title>
<link rel="stylesheet" href="https://fonts.googleapis.com/css2?family=Oswald:wght@300;400&family=Open+Sans:wght@400;600;700&display=swap">
<style>
  :root {
    --ink: #000000;
    --paper: #fbfbfb;
    --charcoal: #333333;
    --steel: #959595;
    --band-dark: #141414;
    --band-mid: #1f1f1f;
    --band-grey: #5a5a5a;
    --backdrop: #d6d6d6;
  }
  * { box-sizing: border-box; margin: 0; padding: 0; }
  html, body {
    width: 1200px; height: 900px; overflow: hidden;
    background: var(--backdrop);
  }
  .canvas {
    position: relative; width: 1200px; height: 900px;
  }
  .card {
    position: absolute; left: 270px; width: 660px; height: 403px;
    background: var(--ink); overflow: hidden;
    box-shadow: 0 6px 18px rgba(0,0,0,0.25);
  }
  .card--back { top: 32px; }
  .card--front { top: 465px; }

  .wordmark {
    font-family: "Oswald", sans-serif; font-weight: 400;
    color: var(--steel); letter-spacing: 2px; text-transform: uppercase;
    white-space: nowrap;
  }
  .brand-square {
    position: absolute; background: var(--steel);
  }

  /* back */
  .card--back .brand-square { left: 40px; top: 40px; width: 150px; height: 150px; background: var(--charcoal); }
  .card--back .wordmark { position: absolute; right: 40px; top: 262px; font-size: 33px; }
  .stripes { position: absolute; left: 0; right: 0; bottom: 0; }
  .stripe { height: var(--h); background: var(--c); }

  /* front */
  .card--front .brand-square { left: 38px; top: 42px; width: 96px; height: 96px; background: var(--charcoal); }
  .card--front .wordmark { position: absolute; left: 160px; top: 128px; font-size: 29px; }
  .agents {
    position: absolute; right: 34px; top: 34px; text-align: right;
    font-family: "Open Sans", sans-serif;
  }
  .agents__names { color: var(--steel); font-weight: 700; font-size: 19px; line-height: 1.2; }
  .agents__role { color: var(--paper); font-size: 15px; margin-top: 2px; }
  .contact-band {
    position: absolute; left: 0; right: 0; top: 200px; height: 132px;
    background: var(--band-dark);
  }
  .contact-band__inner {
    position: absolute; right: 0; top: 66px; bottom: 0; width: 300px;
    background: var(--band-mid);
  }
  .address {
    position: absolute; left: 60px; top: 20px;
    font-family: "Open Sans", sans-serif; font-size: 16px; line-height: 1.35;
    color: var(--paper);
  }
  .phones {
    position: absolute; right: 30px; top: 60px;
    font-family: "Open Sans", sans-serif; font-size: 17px; line-height: 1.5;
    color: var(--paper); list-style: none; text-align: right;
  }
  .phones li { display: flex; align-items: center; justify-content: flex-end; gap: 12px; }
  .phones svg { width: 16px; height: 16px; }
  .card--front .stripes { top: 332px; }
</style>
</head>
<body>
<main class="canvas">

  <section class="card card--back" aria-label="Card back">
    <div class="brand-square" aria-hidden="true"></div>
    <p class="wordmark">Walsh &amp; Brand Pty Ltd.</p>
    <div class="stripes" aria-hidden="true">
      <div class="stripe" style="--h:10px;--c:var(--paper)"></div>
      <div class="stripe" style="--h:26px;--c:var(--band-grey)"></div>
    </div>
  </section>

  <section class="card card--front" aria-label="Card front">
    <div class="brand-square" aria-hidden="true"></div>
    <p class="wordmark">Walsh &amp; Brand Pty Ltd.</p>
    <div class="agents">
      <p class="agents__names">Owen Walsh and Lucy Brand</p>
      <p class="agents__role">Onsite Manager &amp; Sales Agents</p>
    </div>
    <div class="contact-band">
      <div class="contact-band__inner"></div>
      <p class="address">3/42 Marlow Crescent,<br>FERNLEA QLD 4213</p>
      <ul class="phones">
        <li>07 5948 2063
          <svg viewBox="0 0 16 16" aria-label="Phone"><path d="M2 6c0-2 2-3 6-3s6 1 6 3v1h-3V5.5H5V7H2z M4 8h8l1 5H3z" fill="var(--steel)"/></svg>
        </li>
        <li>0431 857 219
          <svg viewBox="0 0 16 16" aria-label="Mobile"><rect x="4" y="1" width="8" height="14" rx="1.5" fill="none" stroke="var(--steel)" stroke-width="1.4"/><circle cx="8" cy="12.5" r="0.9" fill="var(--steel)"/></svg>
        </li>
      </ul>
    </div>
    <div class="stripes" aria-hidden="true">
      <div class="stripe" style="--h:8px;--c:var(--paper)"></div>
      <div class="stripe" style="--h:26px;--c:var(--band-grey)"></div>
      <div class="stripe" style="--h:8px;--c:var(--paper)"></div>
      <div class="stripe" style="--h:29px;--c:var(--band-grey)"></div>
    </div>
  </section>

</main>
</body>
</html>
```